VORELT B2B portal design
Fantastic design work, top communication and fast design changes! Many thanks,Jarek & Lutz from VORELT
Zielgruppe
We are a B2B Cloud Services StartUp that creates B2B logistics & supply chain processes between customer and its suppliers.
Aufgabenstellung
We need a modern responsive able design, that should consider that we are NOT presenting goods or clothes or similar on the portal pages but we show mainly data grids, kpi dashboards, forms, and setting panels to our customer and their suppliers.
The design must be clean and straight not to distract people from the important information in these data grids, kpi dashboards, forms, and settings panels.
We need our logo perfectly embedded and the pages coloured around from grey to blue.
The Designer must be able to deliver a design and transfer it to a highly responsive HTML (5) template (without technical content or further functionality). This our programmers will implement afterwards in .Net.
We need in total 3 page templates:
1. Login Page
2. Main Page with overview over the following services text (each one shown in one tile)
"ZMS (Time Frame Management)"
"DMS (Document Management)"
"REMS (Reporting Management)"
-> Note: At the end we will have up to 12 or more tiles (services) so the design should be additive
3. Data grid (e.g. list of customers)/form (e.g. customer registration form) page to show some data grid with database data
See samples for each page enclosed!!

```html
<!DOCTYPE html>
<html lang="en">
<head>
<meta charset="utf-8">
<title>VORELT – User Registration Form</title>
<link rel="stylesheet" href="https://fonts.googleapis.com/css2?family=Ubuntu:wght@400;500;700&family=Open+Sans:wght@400;600&display=swap">
<style>
  :root {
    --navy: #0d2a44;
    --shell: #e1e6ea;
    --shell-line: #c9d0d6;
    --page: #f2f4f6;
    --card: #ffffff;
    --text: #2b3a47;
    --muted: #5b6670;
    --placeholder: #a4abb2;
    --field-line: #c8ccd0;
    --field-focus: #4f7fae;
    --ok-bg: #e2f2d6;
    --ok-line: #8fcb6a;
    --ok-text: #3a8a1e;
    --err-bg: #f2ddd5;
    --err-line: #d06a4c;
    --err-text: #a7351a;
    --link-red: #e03a2a;
  }
  * { box-sizing: border-box; margin: 0; padding: 0; }
  html, body { width: 1200px; height: 1020px; overflow: hidden; }
  body { position: relative; background: var(--page); font-family: "Ubuntu", sans-serif; color: var(--text); }

  .topbar { position: absolute; left: 0; top: 0; width: 1200px; height: 208px; background: var(--shell); border-bottom: 1px solid #b9c0c6; }
  .brand { position: absolute; left: 24px; top: 64px; display: flex; align-items: center; gap: 14px; }
  .brand-dot { width: 22px; height: 22px; border-radius: 50%; background: var(--navy); }
  .brand-name { font-family: "Ubuntu", sans-serif; font-weight: 700; font-size: 64px; letter-spacing: 2px; color: var(--navy); line-height: 1; }

  .account { position: absolute; right: 28px; top: 70px; display: flex; align-items: center; }
  .account-text { text-align: right; margin-right: 10px; }
  .account-name { font-size: 20px; font-weight: 500; color: var(--navy); }
  .account-role { font-size: 14px; color: var(--muted); margin-top: 1px; }
  .avatar { width: 66px; height: 66px; border-radius: 50%; background: radial-gradient(circle at 50% 40%, #8c8f91, #3d4246); border: 2px solid #9aa2a8; }
  .caret { margin-left: 8px; width: 0; height: 0; border-left: 5px solid transparent; border-right: 5px solid transparent; border-top: 6px solid var(--muted); }

  .sidenav { position: absolute; left: 0; top: 209px; width: 264px; height: 709px; background: var(--shell); }
  .nav-item { height: 61px; display: flex; align-items: center; padding-left: 22px; font-size: 20px; color: var(--navy); border-bottom: 1px solid var(--shell-line); position: relative; }
  .nav-item svg { width: 26px; height: 24px; margin-right: 10px; fill: var(--navy); }
  .nav-item.is-active { background: var(--navy); color: #fff; }
  .nav-item.is-active svg { fill: #fff; }
  .nav-item.logout { border-bottom: none; }
  .nav-arrow { position: absolute; right: 28px; top: 24px; width: 8px; height: 8px; border-top: 2px solid var(--navy); border-right: 2px solid var(--navy); transform: rotate(45deg); }

  .page-title { position: absolute; left: 304px; top: 258px; font-size: 24px; color: #3d4a56; font-weight: 400; }
  .form-card { position: absolute; left: 305px; top: 312px; width: 870px; height: 603px; background: var(--card); box-shadow: 0 2px 0 #d4d8dc; }
  .intro { position: absolute; left: 0; right: 0; top: 45px; text-align: center; font-size: 18px; color: var(--text); }

  .alert { position: absolute; top: 109px; width: 366px; height: 42px; border: 1px solid; font-family: "Open Sans", sans-serif; font-size: 14px; padding: 11px 14px; }
  .alert-success { left: 51px; background: var(--ok-bg); border-color: var(--ok-line); color: var(--ok-text); }
  .alert-error { left: 447px; background: var(--err-bg); border-color: var(--err-line); color: var(--err-text); }

  .field { position: absolute; width: 259px; font-family: "Open Sans", sans-serif; }
  .field label { display: block; font-size: 14px; color: var(--muted); margin-bottom: 9px; }
  .field .input { height: 43px; border: 1px solid var(--field-line); border-radius: 4px; padding: 0 14px; display: flex; align-items: center; font-size: 14px; color: var(--placeholder); }
  .field .input.is-focused { border-color: var(--field-focus); color: var(--text); }
  .field .input.secret { letter-spacing: 3px; font-size: 11px; }
  .f-user { left: 52px; top: 193px; }
  .f-pass { left: 411px; top: 193px; }
  .f-mail { left: 52px; top: 306px; }
  .f-phone { left: 411px; top: 306px; }

  .check { position: absolute; left: 52px; display: flex; align-items: center; font-family: "Open Sans", sans-serif; font-size: 14px; color: var(--muted); }
  .check .box { width: 19px; height: 19px; border-radius: 4px; background: #e3e6e9; border: 1px solid #d2d6da; margin-right: 10px; display: flex; align-items: center; justify-content: center; }
  .check .box svg { width: 11px; height: 9px; stroke: #5b6670; fill: none; stroke-width: 1.6; }
  .check a { color: var(--link-red); text-decoration: none; margin-left: 4px; }
  .c-terms { top: 406px; }
  .c-remember { top: 442px; }

  .btn-register { position: absolute; left: 57px; top: 495px; width: 119px; height: 42px; background: var(--navy); color: #fff; border: none; border-radius: 2px; font-family: "Open Sans", sans-serif; font-size: 14px; letter-spacing: .3px; }

  .footer { position: absolute; left: 0; top: 959px; width: 1200px; height: 61px; background: #fff; border-top: 1px solid #dde1e4; font-family: "Open Sans", sans-serif; font-size: 16px; color: #3d4a56; }
  .footer .copy { position: absolute; left: 14px; top: 19px; }
  .footer .links { position: absolute; right: 22px; top: 19px; }
</style>
</head>
<body>
  <header class="topbar">
    <div class="brand">
      <span class="brand-dot"></span>
      <span class="brand-name">VORELT</span>
    </div>
    <div class="account">
      <div class="account-text">
        <div class="account-name">Dana Morrow</div>
        <div class="account-role">Gest User</div>
      </div>
      <div class="avatar" role="img" aria-label="User profile photo"></div>
      <span class="caret"></span>
    </div>
  </header>

  <nav class="sidenav">
    <div class="nav-item"><svg viewBox="0 0 26 24"><rect x="1" y="6" width="24" height="12" rx="2"/></svg>My News</div>
    <div class="nav-item"><svg viewBox="0 0 26 24"><circle cx="10" cy="7" r="5"/><path d="M1 22c0-6 4-9 9-9s9 3 9 9z"/><circle cx="20" cy="18" r="4"/></svg>My User Settings</div>
    <div class="nav-item is-active"><svg viewBox="0 0 26 24"><circle cx="8" cy="9" r="6"/><circle cx="19" cy="17" r="5"/></svg>Company Settings</div>
    <div class="nav-item"><svg viewBox="0 0 26 24"><path d="M4 21l11-11 2 2L6 23zM14 4a5 5 0 0 1 7 6l-3-1-2-2z"/></svg>Configuration</div>
    <div class="nav-item"><svg viewBox="0 0 26 24"><rect x="2" y="3" width="5" height="4"/><rect x="9" y="3" width="15" height="4"/><rect x="2" y="10" width="5" height="4"/><rect x="9" y="10" width="15" height="4"/><rect x="2" y="17" width="5" height="4"/><rect x="9" y="17" width="15" height="4"/></svg>Services<span class="nav-arrow"></span></div>
    <div class="nav-item"><svg viewBox="0 0 26 24"><ellipse cx="13" cy="11" rx="11" ry="8"/><path d="M5 16l-2 6 7-4z"/></svg>Communication</div>
    <div class="nav-item logout"><svg viewBox="0 0 26 24"><path d="M4 5h8v3H7v11h11v-5h3v8H4z"/><path d="M14 3h9v9l-3-3-6 6-2-2 6-6z"/></svg>Logout</div>
  </nav>

  <h1 class="page-title">User Registration Form</h1>

  <main class="form-card">
    <p class="intro">Please type your account info here.</p>
    <div class="alert alert-success">Success messae</div>
    <div class="alert alert-error">Error messae</div>

    <div class="field f-user"><label>Username:</label><div class="input is-focused">John</div></div>
    <div class="field f-pass"><label>Password:</label><div class="input secret">●●●●●●●</div></div>
    <div class="field f-mail"><label>Mail:</label><div class="input">Type your mail here</div></div>
    <div class="field f-phone"><label>Phone:</label><div class="input">Type your phone here</div></div>

    <div class="check c-terms"><span class="box"><svg viewBox="0 0 11 9"><path d="M1 4.5l3 3 6-6"/></svg></span>I Agree with<a href="#">Terms Of Use</a></div>
    <div class="check c-remember"><span class="box"><svg viewBox="0 0 11 9"><path d="M1 4.5l3 3 6-6"/></svg></span>Remember me</div>

    <button class="btn-register">REGISTER</button>
  </main>

  <footer class="footer">
    <span class="copy">© 2016 VORELT. All rights reserved.</span>
    <span class="links">Help &nbsp;/&nbsp; Disclaimer &nbsp;/&nbsp; Contact</span>
  </footer>
</body>
</html>
```